Vindgerdi - Start-up company selling electricity

Hello let me tell you about Vindgerdi.

Vindgerdi is start-up company selling electricity in Iceland. The operations of the company consist of making power usage forecasts for our customers, purchasing the electricity wholesale from the energy producers, and selling the electricity to the consumer. We are focused on tech by using optimization and machine learning to minimize electricity prices to our customers. Our marketing strategy is to portray a tech company mindset and to show dedication to driving down the electricity price on the market.

We need your help to make our website pop. Possible concepts to work with are as follows:

- Iceland the land of ice and fire
- Green energy
- Innovation
- Tech and data science

Link to our website: https://prufa.vindgerdi-example.is/
We are open to ideas.
Thank you!

Target Market(s)

Electricity consumers both homes and companies.

Number of Pages Required

1 page

Font styles to use
Serif
Sans Serif

```html
<!DOCTYPE html>
<html lang="en">
<head>
<meta charset="utf-8">
<title>Vindgerdi – Same electricity, just cheaper</title>
<link href="https://fonts.googleapis.com/css2?family=Roboto+Slab:wght@400;600;700&family=Poppins:wght@300;400;500;800&family=Rubik:wght@400;500&display=swap" rel="stylesheet">
<style>
:root{
  --navy:#1d3461;
  --red:#a32a22;
  --grey-bg:#f2f4f6;
  --text:#8a8a8a;
  --field:#fbfbfb;
  --line:#e6e6e6;
  --white:#ffffff;
}
*{box-sizing:border-box;margin:0;padding:0}
html,body{width:1200px;height:2992px;overflow:hidden;background:var(--white)}
body{position:relative;font-family:"Poppins",sans-serif;color:var(--text)}
.abs{position:absolute}
.slab{font-family:"Roboto Slab",serif}

/* top bar */
.topbar{left:0;top:0;width:1200px;height:37px;background:var(--navy)}
.topbar-item{top:0;height:37px;display:flex;align-items:center;gap:10px;color:#e8ecf3;font-family:"Roboto Slab",serif;font-size:11.5px}
.dot-icon{width:24px;height:24px;border-radius:50%;background:var(--red);display:flex;align-items:center;justify-content:center}

/* header */
.header{left:0;top:37px;width:1200px;height:76px;background:var(--white)}
.brand{left:60px;top:14px;display:flex;align-items:center;gap:12px}
.brand-mark{width:38px;height:38px;border-radius:50%;background:var(--navy)}
.brand-name{font-family:"Roboto Slab",serif;font-weight:700;font-size:40px;color:var(--red);letter-spacing:.5px}
.nav a{position:absolute;top:32px;font-size:11px;color:#7c7c7c;text-decoration:none;letter-spacing:.3px;text-transform:uppercase}

/* hero */
.hero{left:0;top:113px;width:1200px;height:644px;overflow:hidden}
.hero-photo{position:absolute;inset:0;background:linear-gradient(180deg,#55544c 0%,#7a7870 22%,#a9aaa8 48%,#dfe2e6 72%,#f1f3f5 100%)}
.hero-curve{position:absolute;left:0;top:0}
.hero-title{left:0;width:1200px;top:308px;text-align:center;font-family:"Poppins",sans-serif;font-weight:800;font-size:51px;line-height:60px;color:var(--white);text-shadow:0 2px 6px rgba(0,0,0,.35)}
.hero-lead{left:300px;width:600px;top:433px;text-align:center;font-size:16px;line-height:26px;color:var(--white);text-shadow:0 1px 4px rgba(0,0,0,.4)}
.btn{display:flex;align-items:center;justify-content:center;font-family:"Rubik",sans-serif;font-weight:500;font-size:13.5px;color:var(--white);letter-spacing:.5px;text-transform:uppercase;text-decoration:none;border-radius:18px 0 18px 0;box-shadow:0 4px 8px rgba(0,0,0,.2)}
.btn-red{background:var(--red)}
.btn-navy{background:var(--navy)}

/* mission */
.mission-title{left:136px;top:826px;font-size:36px;font-weight:700;color:var(--navy)}
.mission-title span{color:var(--red);font-weight:400}
.mission-text{left:136px;top:888px;width:530px;font-size:11.5px;line-height:20.3px;color:#8f8f8f;font-weight:300}
.more-link{left:136px;top:1012px;font-family:"Rubik",sans-serif;font-size:11.5px;color:var(--red);display:flex;align-items:center;gap:8px}
.mission-photo{left:755px;top:796px;width:273px;height:305px;background:linear-gradient(180deg,#ffffff 0%,#f4eee8 50%,#e8ddd2 100%)}

/* why choose us */
.why{left:0;top:1101px;width:1200px;height:572px;background:var(--grey-bg);border-top-left-radius:290px 240px}
.section-title{font-family:"Roboto Slab",serif;font-size:35px;font-weight:700;color:var(--navy);text-align:center}
.section-title .soft{color:var(--red);font-weight:400}
.card{top:182px;width:284px;height:299px;background:var(--white);border-radius:40px 0 40px 0;text-align:center}
.card-icon{position:absolute;left:110px;top:-38px;width:75px;height:75px;background:var(--navy);display:flex;align-items:center;justify-content:center}
.card h3{margin-top:66px;font-family:"Poppins",sans-serif;font-weight:400;font-size:22px;color:#1a1a1a}
.card p{margin:18px auto 0;width:235px;font-size:11.5px;line-height:20.3px;color:#9a9a9a;font-weight:300}
.card-go{position:absolute;left:127px;bottom:-15px;width:30px;height:30px;border-radius:50%;background:var(--navy);display:flex;align-items:center;justify-content:center}
.price-row{position:absolute;left:75px;display:flex;align-items:flex-start;gap:10px;text-align:left}
.price-num{font-family:"Poppins",sans-serif;font-weight:500;font-size:31px;color:var(--red);line-height:34px;width:66px}
.price-unit{font-size:12px;color:var(--navy);line-height:20px;padding-top:9px}
.card .compare{position:absolute;left:0;width:100%;top:230px;margin:0;font-size:14.5px;line-height:20px;color:#555;font-weight:400}

/* request form */
.form-title{left:0;width:1200px;top:1744px;font-family:"Roboto Slab",serif;font-size:35px;line-height:42px;text-align:center;color:var(--navy);font-weight:600}
.form-title .soft{color:var(--red);font-weight:400}
.field{height:45px;background:var(--field);border:1px solid var(--line);font-size:11.5px;color:#9c9c9c;padding:0 12px;display:flex;align-items:center}

/* call to action */
.cta{left:0;top:2265px;width:1200px;height:358px;background:linear-gradient(180deg,#2b4573 0%,#24406d 60%,#203a64 100%)}
.cta-title{left:0;width:1200px;top:2336px;text-align:center;font-family:"Roboto Slab",serif;font-size:35px;line-height:42px;color:var(--white);font-weight:400}
.cta-lead{left:380px;width:440px;top:2433px;text-align:center;font-size:11.5px;line-height:20.3px;color:#dfe5ef}

/* footer */
.footer{left:0;top:2623px;width:1200px;height:369px;background:var(--red)}
.foot-brand{left:60px;top:2700px;display:flex;align-items:center;gap:10px}
.foot-brand .brand-mark{width:26px;height:26px;background:var(--white)}
.foot-brand .brand-name{color:var(--white);font-size:26px}
.foot-head{top:2700px;font-family:"Roboto Slab",serif;font-weight:700;font-size:14.5px;color:var(--white);text-transform:uppercase}
.foot-list{top:2735px;list-style:none;font-size:11.5px;color:#f7dcd9;line-height:22.6px}
.foot-list li::before{content:"-  ";white-space:pre}
.contact-row{left:889px;display:flex;align-items:center;gap:17px;font-size:11.5px;color:#fbe8e6}
.contact-dot{width:34px;height:34px;border-radius:50%;background:var(--white);display:flex;align-items:center;justify-content:center}
.foot-rule{left:0;top:2925px;width:1200px;height:1px;background:rgba(255,255,255,.15)}
.copyright{left:0;width:1200px;top:2952px;text-align:center;font-size:9.5px;color:#f3d3cf}
</style>
</head>
<body>

<div class="abs topbar"></div>
<div class="abs topbar-item" style="left:476px">
  <span class="dot-icon"><svg width="11" height="13" viewBox="0 0 12 14"><path d="M6 0a5 5 0 0 0-5 5c0 3.6 5 9 5 9s5-5.4 5-9a5 5 0 0 0-5-5zm0 7a2 2 0 1 1 0-4 2 2 0 0 1 0 4z" fill="#fff"/></svg></span>
  Ljósvegur 4, 200 Kópavogur
</div>
<div class="abs topbar-item" style="left:724px">
  <span class="dot-icon"><svg width="12" height="12" viewBox="0 0 24 24"><path d="M6.6 10.8a15 15 0 0 0 6.6 6.6l2.2-2.2c.3-.3.7-.4 1-.2 1.1.4 2.3.6 3.6.6.6 0 1 .4 1 1V20c0 .6-.4 1-1 1A17 17 0 0 1 3 4c0-.6.4-1 1-1h3.5c.6 0 1 .4 1 1 0 1.3.2 2.5.6 3.6.1.3 0 .7-.2 1z" fill="#fff"/></svg></span>
  Email Us : hallo@vindgerdi-example.is
</div>
<div class="abs topbar-item" style="left:994px">
  <span class="dot-icon"><svg width="12" height="10" viewBox="0 0 24 18"><rect x="1" y="1" width="22" height="16" rx="2" fill="#fff"/><path d="M2 2l10 8 10-8" stroke="#a32a22" stroke-width="2" fill="none"/></svg></span>
  Call Us : 555-0142
</div>

<header class="abs header">
  <div class="abs brand"><span class="brand-mark"></span><span class="brand-name">VINDGERDI</span></div>
  <nav class="nav">
    <a style="left:698px">Terms of business</a>
    <a style="left:837px">Question &amp; Answer</a>
    <a style="left:987px">About Vindgerdi</a>
  </nav>
  <svg class="abs" style="left:1125px;top:30px" width="16" height="16" viewBox="0 0 16 16"><circle cx="6.5" cy="6.5" r="5" stroke="#a32a22" stroke-width="1.5" fill="none"/><path d="M10.2 10.2L15 15" stroke="#a32a22" stroke-width="1.5"/></svg>
</header>

<section class="abs hero">
  <div class="hero-photo" role="img" aria-label="Snowy winter landscape with a wooden farmhouse and frosted trees under a cloudy sky"></div>
  <svg class="hero-curve" width="1200" height="644" viewBox="0 0 1200 644">
    <path d="M0 644 L0 638 L930 638 C1090 638 1194 520 1200 340 L1200 644 Z" fill="#ffffff"/>
    <path d="M0 638 L930 638 C1090 638 1194 520 1200 340" fill="none" stroke="#a32a22" stroke-width="7"/>
  </svg>
</section>
<h1 class="abs hero-title">SAME ELECTRICITY<br>JUST CHEAPER!</h1>
<p class="abs hero-lead">Lorem ipsum dolor sit amet, consectetur adipiscing elit, sed do eiusmod tempor incididunt ut labore et dolore magna aliqua.</p>
<a class="abs btn btn-red" style="left:455px;top:507px;width:135px;height:44px">Contact us</a>
<a class="abs btn btn-navy" style="left:605px;top:507px;width:135px;height:44px">Learn more</a>

<h2 class="abs slab mission-title"><span>OUR</span> MISSION</h2>
<p class="abs mission-text">Lorem ipsum dolor sit amet, consectetur adipiscing elit, sed do eiusmod tempor incididunt ut labore et dolore magna aliqua. Ut enim ad minim veniam, quis nostrud exercitation tog ullamco laboris nisi ut aliquip ex ea commodo consequat. Duis aute irure dolor in theregh reprehenderit in voluptate velit esse cillum dolore eu fugiat nulla pariatur. Excepteur sint occaecat cupidatat non proident, sunt in culpa qui officia deserunt mollit anim</p>
<a class="abs more-link">MORE ABOUT US <svg width="9" height="11" viewBox="0 0 9 11"><path d="M0 0L9 5.5 0 11z" fill="#a32a22"/></svg></a>
<div class="abs mission-photo" role="img" aria-label="Photo of two hands holding up a lit light bulb"></div>

<section class="abs why">
  <h2 class="section-title" style="margin-top:71px"><span class="soft">WHY</span> CHOOSE US</h2>

  <div class="abs card" style="left:135px">
    <div class="card-icon"><svg width="38" height="46" viewBox="0 0 38 46" fill="none" stroke="#fff" stroke-width="2"><path d="M14 2v8M24 2v8"/><rect x="9" y="10" width="20" height="12" rx="2"/><path d="M13 22v5a6 6 0 0 0 12 0v-5"/><path d="M19 33v4c0 4-4 7-8 7H4"/><path d="M6 26c-3 0-4 4-2 6"/></svg></div>
    <h3>Welcome to business</h3>
    <p>Lorem ipsum dolor sit amet, consectetur adipiscing elit, sed do eiusmod tempor incididunt ut labore et dolore magna aliqua. Ut enim ad minim veniam, quis nostrud exercitation .</p>
    <span class="card-go"><svg width="12" height="12" viewBox="0 0 12 12" fill="none" stroke="#fff" stroke-width="1.6"><path d="M2 2l4 4-4 4M6 2l4 4-4 4"/></svg></span>
  </div>

  <div class="abs card" style="left:458px">
    <div class="card-icon"><svg width="36" height="48" viewBox="0 0 36 48" fill="none" stroke="#fff" stroke-width="2"><rect x="3" y="6" width="30" height="40" rx="3"/><rect x="12" y="2" width="12" height="7" rx="2"/><path d="M9 17h6M12 14v6M19 17h9M19 22h9M9 29h10M9 34h10M9 39h10"/><path d="M28 28c-2-2-6-1-5 1s5 1 5 4-4 3-6 1M25 26v12"/></svg></div>
    <h3>Price list</h3>
    <div class="price-row" style="top:110px"><span class="price-num">6.95</span><span class="price-unit">ISK / kWh</span></div>
    <div class="price-row" style="top:155px"><span class="price-num">6.22</span><span class="price-unit">ISK / kWhelectric<br>acceleration</span></div>
    <p class="compare">Make a price comparison</p>
    <span class="card-go"><svg width="12" height="12" viewBox="0 0 12 12" fill="none" stroke="#fff" stroke-width="1.6"><path d="M2 2l4 4-4 4M6 2l4 4-4 4"/></svg></span>
  </div>

  <div class="abs card" style="left:781px">
    <div class="card-icon"><svg width="30" height="48" viewBox="0 0 30 48" fill="none" stroke="#fff" stroke-width="2" stroke-linejoin="round"><path d="M20 2L4 27h10l-4 19L26 20H15z"/></svg></div>
    <h3>The future is exciting</h3>
    <p>Let's make the electricity system smarter together. Vindgerdi uses artificial intelligence, data science and automation to minimize costs and promote eccentricity</p>
    <span class="card-go"><svg width="12" height="12" viewBox="0 0 12 12" fill="none" stroke="#fff" stroke-width="1.6"><path d="M2 2l4 4-4 4M6 2l4 4-4 4"/></svg></span>
  </div>
</section>

<h2 class="abs form-title"><span class="soft">REQUEST AN OFFER FOR</span><br>ELECTRICITY PRICES</h2>
<form>
  <div class="abs field" style="left:270px;top:1860px;width:210px">Name &nbsp;:</div>
  <div class="abs field" style="left:495px;top:1860px;width:210px">Phone &nbsp;:</div>
  <div class="abs field" style="left:720px;top:1860px;width:210px">Email &nbsp;:</div>
  <div class="abs field" style="left:270px;top:1920px;width:210px">Address &nbsp;:</div>
  <div class="abs field" style="left:495px;top:1920px;width:210px">Post number &nbsp;:</div>
  <div class="abs field" style="left:720px;top:1920px;width:210px">Company contact &nbsp;:</div>
  <div class="abs field" style="left:270px;top:1980px;width:660px">Social Security number &nbsp;:</div>
  <div class="abs field" style="left:270px;top:2040px;width:660px;height:90px"></div>
  <a class="abs btn btn-red" style="left:497px;top:2145px;width:202px;height:45px">Send a quote request</a>
</form>

<section class="abs cta" role="img" aria-label="Power line pylons and wind turbines in a blue-toned field"></section>
<h2 class="abs cta-title">WHAT ARE YOU STILL<br>LOOKING FOR?</h2>
<p class="abs cta-lead">Lorem ipsum dolor sit amet, consectetur adipiscing elit, sed do eiusmod tempor incididunt ut labore et dolore magna aliqua.</p>
<a class="abs btn btn-red" style="left:538px;top:2497px;width:122px;height:45px">Contact us</a>

<footer class="abs footer"></footer>
<svg class="abs" style="left:0;top:2420px" width="1200" height="210" viewBox="0 0 1200 210">
  <path d="M0 210 L0 199 L960 199 C1110 199 1194 110 1200 0 L1200 210 Z" fill="#a32a22"/>
  <path d="M0 199 L960 199 C1110 199 1194 110 1200 0" fill="none" stroke="#ffffff" stroke-width="7"/>
</svg>

<div class="abs foot-brand"><span class="brand-mark"></span><span class="brand-name">VINDGERDI</span></div>

<h4 class="abs foot-head" style="left:337px">Vindgerdi ehf</h4>
<ul class="abs foot-list" style="left:337px">
  <li>ID number: 610318-2270</li>
  <li>VAT number: 204417</li>
</ul>

<h4 class="abs foot-head" style="left:613px">Links</h4>
<ul class="abs foot-list" style="left:613px">
  <li>Terms of business</li>
  <li>Question &amp; Answer</li>
  <li>About Vindgerdi</li>
</ul>

<h4 class="abs foot-head" style="left:889px">Get in touch</h4>
<div class="abs contact-row" style="top:2735px">
  <span class="contact-dot"><svg width="13" height="16" viewBox="0 0 12 14"><path d="M6 0a5 5 0 0 0-5 5c0 3.6 5 9 5 9s5-5.4 5-9a5 5 0 0 0-5-5zm0 7a2 2 0 1 1 0-4 2 2 0 0 1 0 4z" fill="#1d3461"/></svg></span>
  Ljósvegur 4, 200 Kópavogur
</div>
<div class="abs contact-row" style="top:2780px">
  <span class="contact-dot"><svg width="14" height="14" viewBox="0 0 24 24"><path d="M6.6 10.8a15 15 0 0 0 6.6 6.6l2.2-2.2c.3-.3.7-.4 1-.2 1.1.4 2.3.6 3.6.6.6 0 1 .4 1 1V20c0 .6-.4 1-1 1A17 17 0 0 1 3 4c0-.6.4-1 1-1h3.5c.6 0 1 .4 1 1 0 1.3.2 2.5.6 3.6.1.3 0 .7-.2 1z" fill="#1d3461"/></svg></span>
  hallo@vindgerdi-example.is
</div>
<div class="abs contact-row" style="top:2826px">
  <span class="contact-dot"><svg width="14" height="11" viewBox="0 0 24 18"><rect x="1" y="1" width="22" height="16" rx="2" fill="#1d3461"/><path d="M2 2l10 8 10-8" stroke="#fff" stroke-width="2" fill="none"/></svg></span>
  555-0142
</div>

<div class="abs foot-rule"></div>
<p class="abs copyright">Copyright © Vindgerdi 2020 - All rights reserved</p>

</body>
</html>
```